School Website

I need a design for a School (2 sections: Primary 6-12 years and Secondary 12-18 years). The first page is just a choice of the 2 sections. After we'll need 2 websites (with the same structure: Menu, ...) but with different colors. In fact, we need for end of October, 6 design of school website. So the best websites are going to be made available to you in the future (in pixelharbor) but privately.

Target Market(s)

Public, Parents, ...

Coding

Coded - Design and coding required

Number of Pages Required

5+ page

Font styles to use
Sans Serif

Colors
34a6d7
85cae6
cee9f5
ffffff

Requirements
Must have
• You can check the old Website: http: / /velmot.be We need the same pages with the same content. Menu: - HomePage - News and communication (like blog page) - Activities (like blog page, with photo gallery) - Contact (Contact form + maps) - In the main menu, we need a special button to connect to an external Website ( button needs to be different than the other menu items The name of this button is "Parents Area"). The logo of 2 sections are attached. Please use it for the design and the choice of colors.
Nice to have
• This is a web design of other school that we like: https://www.quintelo.be

```html
<!DOCTYPE html>
<html lang="fr">
<head>
<meta charset="utf-8">
<title>Athénée Royal de Merlon – Maternelles et Primaires</title>
<link href="https://fonts.googleapis.com/css2?family=Raleway:ital,wght@0,400;0,500;0,600;0,700;1,400&display=swap" rel="stylesheet">
<style>
  :root {
    --page-bg: #d5ebf6;
    --band-bg: #cfe6f3;
    --brand-blue: #34a6d7;
    --soft-blue: #85cae6;
    --pale-blue: #cee9f5;
    --white: #ffffff;
    --accent-orange: #f05a28;
    --text-grey: #666a6e;
    --text-dark: #333638;
    --board-dark: #2e3133;
    --board-mid: #45494c;
  }
  * { margin: 0; padding: 0; box-sizing: border-box; }
  html, body { width: 686px; height: 1200px; overflow: hidden; background: var(--page-bg); }
  body { font-family: "Raleway", sans-serif; color: var(--text-grey); }
  .canvas { position: relative; width: 686px; height: 1200px; overflow: hidden; background: var(--page-bg); }
  .abs { position: absolute; }

  /* Hero */
  .hero { left: 103px; top: 1px; width: 480px; height: 235px; overflow: hidden;
    background: radial-gradient(ellipse at 78% 60%, #5d7fa3 0%, #4b6280 18%, var(--board-mid) 40%, var(--board-dark) 100%); }
  .hero-nav { left: 0; top: 0; width: 480px; height: 31px; background: rgba(90,100,110,.55); }
  .brand { left: 8px; top: 9px; display: flex; align-items: center; gap: 3px; font-size: 7px; font-weight: 600; color: var(--white); }
  .brand-dot { width: 7px; height: 7px; border-radius: 50%; background: var(--soft-blue); }
  .nav-item { top: 12px; font-size: 6.8px; font-weight: 500; color: var(--white); white-space: nowrap; }
  .parents-btn { left: 422px; top: 5px; width: 53px; height: 21px; border-radius: 6px; background: var(--accent-orange);
    color: var(--white); font-size: 7px; font-weight: 600; display: flex; align-items: center; justify-content: center; }
  .hero-divider { left: 181px; top: 21px; width: 0.6px; height: 214px; background: rgba(255,255,255,.55); }
  .hero-title { left: 9px; top: 61px; font-size: 17.5px; font-weight: 700; color: var(--white); white-space: nowrap; }
  .hero-title span { color: var(--brand-blue); }
  .hero-sub { left: 8px; top: 88px; font-size: 10.5px; font-weight: 500; color: var(--white); }
  .hero-text { left: 9px; top: 109px; width: 120px; font-size: 7px; line-height: 10.4px; color: var(--white); }
  .partner-name { left: 9px; top: 210px; font-size: 6.5px; font-weight: 600; color: var(--white); }

  /* Section headings */
  .big-title { font-size: 24.5px; line-height: 28.5px; font-weight: 500; letter-spacing: .6px; color: var(--white); }
  .big-title .blue { color: var(--brand-blue); }
  .para { font-size: 6.7px; line-height: 10.3px; color: var(--text-grey); }

  /* About */
  .about-mark { left: 112px; top: 269px; width: 15px; height: 15px; border-radius: 50%; background: var(--soft-blue); }
  .about-title { left: 111px; top: 285px; }
  .about-text { left: 381px; top: 287px; width: 160px; }
  .contact-line { top: 404px; font-size: 5.8px; color: var(--text-grey); white-space: nowrap; }

  /* Staff */
  .avatar { width: 34px; height: 34px; border-radius: 50%; border: 1.2px solid var(--brand-blue);
    background: radial-gradient(circle at 50% 40%, #d9b8a0 0%, #9c7257 55%, #5a3d2c 100%); }
  .staff { left: 172px; width: 90px; }
  .staff-name { font-size: 6.8px; font-weight: 500; color: var(--text-dark); }
  .staff-role { font-size: 5.6px; font-style: italic; color: var(--text-grey); margin-top: 2px; }
  .staff-bio { font-size: 6.7px; line-height: 10px; color: var(--text-grey); margin-top: 3px; }
  .staff-mail { font-size: 6.7px; color: var(--brand-blue); margin-top: 1px; }
  .arrow { width: 12px; height: 22px; }
  .dots { display: flex; gap: 4.6px; }
  .dot { width: 4px; height: 4px; border-radius: 50%; border: 0.8px solid var(--brand-blue); }
  .dot.active { background: var(--brand-blue); }
  .teacher-icon { left: 507px; top: 446px; width: 22px; height: 23px; border-radius: 4px;
    background: linear-gradient(180deg, #4a4f66 0%, #e8c9a8 45%, #8c6e55 100%); }
  .staff-title { left: 381px; top: 470px; }

  /* Calendar */
  .calendar-band { left: 103px; top: 601px; width: 480px; height: 163px; background: var(--band-bg); }
  .cal-title { left: 111px; top: 646px; }
  .cal-list { left: 346px; top: 648px; width: 200px; list-style: none; }
  .cal-list li { position: relative; padding-left: 6px; font-size: 6.7px; line-height: 10.3px; color: var(--text-grey); margin-bottom: 3.8px; }
  .cal-list li::before { content: ""; position: absolute; left: 0; top: 2px; width: 1.8px; height: 1.8px; border-radius: 50%; background: var(--text-dark); }
  .cal-link { left: 489px; top: 770px; font-size: 6.8px; color: var(--accent-orange); white-space: nowrap; }

  /* News */
  .news-icon { left: 490px; top: 797px; width: 24px; height: 24px; border-radius: 50%; background: var(--accent-orange); }
  .news-title { left: 381px; top: 822px; }
  .news-text { left: 125px; top: 825px; width: 140px; }
  .news-more { color: var(--accent-orange); }
  .news-meta { left: 125px; top: 879px; font-size: 5.2px; line-height: 10px; font-style: italic; color: var(--text-grey); }

  /* Footer */
  .footer { left: 103px; top: 956px; width: 480px; height: 203px; background: var(--brand-blue); color: var(--white); }
  .footer-heading { left: 8px; top: 19px; font-size: 6.8px; font-weight: 700; }
  .field { border-bottom: 0.6px solid var(--white); font-size: 5px; font-style: italic; padding-left: 1px; height: 10px; }
  .send-btn { left: 9px; top: 103px; width: 51px; height: 17px; border: 0.8px solid var(--white); border-radius: 2px;
    font-size: 7px; display: flex; align-items: center; justify-content: center; }
  .footer-info { left: 8px; top: 132px; font-size: 6px; line-height: 10.5px; }
  .social { top: 179px; width: 13px; height: 13px; border-radius: 50%; background: var(--pale-blue); }
  .map { left: 244px; top: 19px; width: 226px; height: 123px;
    background: linear-gradient(115deg, #a9dbef 0%, #a9dbef 22%, #3eaedc 26%, #3aa9d9 100%); }
  .copyright { left: 0; top: 192px; width: 480px; text-align: center; font-size: 5px; color: var(--pale-blue); }
</style>
</head>
<body>
<div class="canvas">

  <!-- Hero -->
  <header class="abs hero" role="img" aria-label="Photo d'une élève à lunettes tenant des cahiers colorés devant un tableau noir">
    <div class="abs hero-nav"></div>
    <div class="abs brand"><span class="brand-dot"></span>Merlon</div>
    <span class="abs nav-item" style="left:58px">maternelle-primaire</span>
    <span class="abs nav-item" style="left:141px">secondaire</span>
    <span class="abs nav-item" style="left:192px">Activités</span>
    <span class="abs nav-item" style="left:234px">Galerie</span>
    <span class="abs nav-item" style="left:271px">Contactez-nous</span>
    <a class="abs parents-btn">Zone Parents</a>
    <div class="abs hero-divider"></div>
    <h1 class="abs hero-title"><span>Athénée Royal</span> de Merlon</h1>
    <h2 class="abs hero-sub">Maternelles et Primaires</h2>
    <p class="abs hero-text">Lorem ipsum dolor sit amet, consectetur adipiscing elit. Phasellus ultricies lectus a nibh luctus, ut malesuada magna</p>
    <div class="abs partner-name">Réseau Scolaire</div>
  </header>

  <!-- About -->
  <div class="abs about-mark"></div>
  <h2 class="abs big-title about-title">Sur<br><span class="blue">Athénée Royal</span><br>de Merlon</h2>
  <p class="abs para about-text">Lorem ipsum dolor sit amet, consectetur adipiscing elit. Phasellus ultricies lectus a nibh luctus, ut malesuada magna accumsan. Donec consectetur, quam et pretium feugiat, ligula orci viverra purus, et lacinia lectus sapien vel metus. Praesent sed sem tortor. Nunc ac est nisl. Curabitur consectetur luctus velit id maximus. Praesent facilisis sodales</p>
  <span class="abs contact-line" style="left:111px">Rue des Tilleuls 12, 4520 Merlon, Belgique</span>
  <span class="abs contact-line" style="left:292px">+32-80 00 41 17</span>

  <!-- Staff -->
  <div class="abs avatar" style="left:129px;top:445px" role="img" aria-label="Portrait de l'enseignante Lena Verhoef"></div>
  <div class="abs staff" style="top:449px">
    <div class="staff-name">Lena Verhoef</div>
    <div class="staff-role">science</div>
    <div class="staff-bio">Lorem ipsum dolor sit amet, consectetur adipiscing elit. Phasellus</div>
    <div class="staff-mail">lenaverhoef@merlon.be</div>
  </div>
  <div class="abs avatar" style="left:129px;top:515px" role="img" aria-label="Portrait de l'enseignante Marthe Delcourt"></div>
  <div class="abs staff" style="top:519px">
    <div class="staff-name">Marthe Delcourt</div>
    <div class="staff-role">math</div>
    <div class="staff-bio">Lorem ipsum dolor sit amet, consectetur adipiscing elit. Phasellus</div>
    <div class="staff-mail">marthedelcourt@merlon.be</div>
  </div>
  <svg class="abs arrow" style="left:103px;top:494px" viewBox="0 0 12 22"><polyline points="11,1 1,11 11,21" fill="none" stroke="#34a6d7" stroke-width="1.3"/></svg>
  <svg class="abs arrow" style="left:321px;top:494px" viewBox="0 0 12 22"><polyline points="1,1 11,11 1,21" fill="none" stroke="#34a6d7" stroke-width="1.3"/></svg>
  <div class="abs dots" style="left:210px;top:596px"><span class="dot active"></span><span class="dot"></span><span class="dot"></span><span class="dot"></span><span class="dot"></span></div>
  <div class="abs teacher-icon" role="img" aria-label="Illustration d'un professeur avec toque de diplômé"></div>
  <h2 class="abs big-title staff-title">Rencontrez<br>notre<br><span class="blue">personnel</span></h2>

  <!-- Calendar -->
  <section class="abs calendar-band"></section>
  <svg class="abs" style="left:112px;top:621px" width="21" height="23" viewBox="0 0 21 23">
    <rect x="0.5" y="3" width="20" height="19.5" rx="2" fill="#ffffff"/>
    <path d="M0.5 5a2 2 0 0 1 2-2h16a2 2 0 0 1 2 2v3.5h-20z" fill="#8e5fc1"/>
    <rect x="4" y="0.5" width="2" height="5" rx="1" fill="#f5c518"/>
    <rect x="15" y="0.5" width="2" height="5" rx="1" fill="#f5c518"/>
    <text x="10.5" y="19" text-anchor="middle" font-family="Raleway, sans-serif" font-size="8" font-weight="600" fill="#8e5fc1">31</text>
  </svg>
  <h2 class="abs big-title cal-title"><span class="blue">Calenderier</span><br>et<br>Vacances</h2>
  <ul class="abs cal-list">
    <li>L'établissement sera ouvert jusqu'au 5 juillet 2018 inclus et à partir du 16 août 2018 de 9h à 15h.</li>
    <li>Rentrée scolaire: lundi 3 septembre.</li>
    <li>Fête de la Communauté française : jeudi 27 septembre.</li>
    <li>Congé d'automne (Toussaint) : Du lundi 29 octobre au vendredi 2 novembre 2018</li>
    <li>Vacances d'hiver (Noël) : Du lundi 24 décembre 2018 au vendredi 4 janvier 2019</li>
  </ul>
  <a class="abs cal-link">voir le calendrier complet</a>

  <!-- News -->
  <div class="abs news-icon" role="img" aria-label="Icône globe des nouvelles"></div>
  <h2 class="abs big-title news-title"><span class="blue">Nouvelles</span><br>et<br>Activites</h2>
  <p class="abs para news-text">Visite du rucher école de la ville de Merlon avec les 6èmes Sciences – génétique et écologie des pollinisateurs.<br><span class="news-more">Lire la suite</span></p>
  <p class="abs news-meta">18 septembre 2018<br>rucher école, ville de Merlon</p>
  <svg class="abs arrow" style="left:102px;top:860px" viewBox="0 0 12 22"><polyline points="11,1 1,11 11,21" fill="none" stroke="#34a6d7" stroke-width="1.3"/></svg>
  <svg class="abs arrow" style="left:320px;top:860px" viewBox="0 0 12 22"><polyline points="1,1 11,11 1,21" fill="none" stroke="#34a6d7" stroke-width="1.3"/></svg>
  <div class="abs dots" style="left:179px;top:939px"><span class="dot active"></span><span class="dot"></span><span class="dot"></span><span class="dot"></span></div>

  <!-- Footer -->
  <footer class="abs footer">
    <h3 class="abs footer-heading">Contactez-nous</h3>
    <div class="abs field" style="left:8px;top:35px;width:64px">Nom</div>
    <div class="abs field" style="left:79px;top:35px;width:64px">Adresse e-mail</div>
    <div class="abs field" style="left:8px;top:64px;width:135px;height:27px">Message</div>
    <div class="abs send-btn">Envoyer</div>
    <p class="abs footer-info">Rue des Tilleuls 12,<br>4520 Merlon, Belgique<br>+32-80 00 41 17<br>Du lundi au vendredi 7.00- 18.00</p>
    <span class="abs social" style="left:9px"></span>
    <span class="abs social" style="left:26px"></span>
    <span class="abs social" style="left:44px"></span>
    <div class="abs map" role="img" aria-label="Plan du quartier de l'école avec la rivière et un repère de localisation"></div>
    <p class="abs copyright">2019 Tous droits réservés. Athénée Royal de Merlon</p>
  </footer>

</div>
</body>
</html>
```